AUTOMOTIVE/ CAR REPAIRS / CRASH REPAIRS / PAINT SPRAYING AND PANEL BEATING

AUTOMOTIVE REPAIR. CAR / MOTORCYCLES GOT LOGO DESIGN / DID THINK ABOUT FACEBOOK DONT NOALREADY HAVE WEB ADRESS www.brenvashine.co.uk and mail sales@brenvashine,co.uk NEED SOMETHINK I CAN MANAGE TO UPLOAD PICTURES IN TO A GALLERY OR SOMETHINGLIKE THAT I ALSO SELL CAR AND MOTORCYCLES MAYBE A SELLS PAGE WITH A TILLWAVE LINK

Target Market(s)

TRADE / GENERAL PUBLIC

Industry/Entity Type

Automotive

Coding

Coded - Design and coding required

Number of Pages Required

4 page

Font styles to use
Serif
Sans Serif

Colors

Designer to choose colors to be used in the design.

Requirements
Must have
• GALLERY/ SHOP TO SALE CARS AND MOTORCYCLE / LOGOS OF MATERIALS I USE DORFLINT / KEBO / VASTINCO / Q WRAP / GLENBRUSH
• CONTACT US
Nice to have
• TILLWAVE / EASY TO MANAGE / VIDEO CLIP OF DORFLINT HUE PLANNER Z7
• SWIFT BLEND PAINT TONVIEW WETLINE AND TULVOKE

```html
<!DOCTYPE html>
<html lang="en">
<head>
<meta charset="utf-8">
<title>Brenvashine Bodyshop</title>
<link rel="stylesheet" href="https://fonts.googleapis.com/css2?family=Poppins:wght@400;500;600&family=Roboto:wght@500;700&display=swap">
<style>
:root{
  --ink:#15171f;
  --ink-deep:#0e1017;
  --red:#a11d2a;
  --red-deep:#7e1520;
  --red-text:#c41e2e;
  --white:#ffffff;
  --grey-bg:#efefef;
  --text:#1d1d1d;
  --muted:#555;
  --line:#9a9a9a;
  --head:'Roboto',sans-serif;
  --body:'Poppins',sans-serif;
}
*{margin:0;padding:0;box-sizing:border-box}
html,body{width:1200px;height:3908px;overflow:hidden;background:var(--white);font-family:var(--body);color:var(--text)}
.page{position:relative;width:1200px;height:3908px}
.abs{position:absolute}
.center{text-align:center;left:0;width:1200px}

/* header */
.site-header{top:0;left:0;width:1200px;height:108px;background:var(--ink)}
.brand{left:114px;top:18px;width:356px;color:var(--white);text-align:center}
.brand-name{font-family:var(--body);font-weight:600;font-size:40px;letter-spacing:3px;line-height:48px}
.brand-sub{font-size:17px;letter-spacing:14px;line-height:24px}
.top-contact{top:20px;font-size:18px;font-weight:600;color:var(--white);display:flex;align-items:center;gap:6px}
.nav{top:70px;left:0;width:1200px;font-size:17px;font-weight:500;color:var(--white)}
.nav span{position:absolute;top:0}
.nav .active{border-bottom:2px solid var(--white);padding-bottom:2px}

/* hero */
.hero{top:108px;left:0;width:1200px;height:598px;background:linear-gradient(115deg,#3a3a44 0%,#1b2a44 30%,#123a63 55%,#3d6c99 72%,#8a4a2a 92%,#2b1d1d 100%)}
.hero-title{top:250px;font-size:45px;color:var(--white);font-weight:500}
.hero-sub{top:306px;font-size:22px;color:var(--white);font-weight:500;line-height:29px}
.hero-btn{top:405px;left:467px;width:133px;height:48px;border:2px solid var(--white);color:var(--white);font-family:var(--head);font-weight:700;font-size:17px;display:flex;align-items:center;justify-content:center}
.dots{top:650px;left:571px;display:flex;gap:8px}
.dots i{display:block;width:14px;height:14px;border:2px solid var(--white);border-radius:50%}
.dots i.on{background:var(--white)}

/* welcome */
.welcome-title{top:774px;font-family:var(--head);font-weight:700;font-size:34px;line-height:42px;color:var(--ink)}
.welcome-text{top:894px;left:130px;width:940px;text-align:center;font-size:16px;line-height:29px;font-weight:500}
.outline-btn{top:1013px;left:520px;width:158px;height:53px;border:2px solid #999;color:var(--red-text);font-family:var(--head);font-weight:700;font-size:17px;display:flex;align-items:center;justify-content:center;gap:6px}
.photo-round{border-radius:50%;border:4px solid var(--ink)}
.circle-label{font-family:var(--head);font-weight:700;font-size:17px;width:300px;text-align:center;color:var(--ink)}
.feature{top:1135px;left:439px;width:324px;height:324px;border-radius:50%;background:var(--red-deep);border:6px solid var(--red);color:var(--white);text-align:center}
.feature h3{font-family:var(--head);font-weight:700;font-size:21px;margin-top:72px}
.feature p{font-size:14px;line-height:28px;margin:14px 30px 0}

/* services */
.services{top:1538px;left:0;width:1200px;height:730px;background:var(--ink)}
.services-photo{top:0;left:0;width:600px;height:730px;background:linear-gradient(90deg,#0b0b0e 0%,#24262c 30%,#0c0d11 48%,#1a7d93 50%,#0d2333 56%,#12202c 100%)}
.services h2{top:76px;left:671px;font-family:var(--head);font-weight:700;font-size:35px;color:var(--white)}
.svc{left:672px;display:flex;align-items:center;gap:22px;color:var(--white);font-family:var(--head);font-weight:700;font-size:21px;line-height:28px}
.svc-ico{width:88px;height:88px;border-radius:50%;background:var(--red);flex:none;display:flex;align-items:center;justify-content:center}

/* gallery */
.section-title{font-family:var(--head);font-weight:700;font-size:35px;color:var(--ink)}
.thumb{width:223px;height:166px}

/* partners */
.partner{top:2920px;width:224px;height:88px;border:1px solid #ddd;box-shadow:0 2px 5px rgba(0,0,0,.2);display:flex;align-items:center;justify-content:center;font-family:var(--body);font-weight:600;font-size:24px;color:var(--red);background:var(--white)}

/* appointment */
.appointment{top:3095px;left:0;width:1200px;height:493px;background:var(--grey-bg)}
.appointment h2{top:68px}
.appt-addr{top:126px;font-family:var(--head);font-weight:500;font-size:21px;line-height:29px;color:#333}
.field{height:50px;border:1px solid var(--line);background:var(--white);font-size:14px;color:#444;padding-left:20px;display:flex;align-items:center}
.submit{top:350px;left:554px;width:92px;height:43px;border:1px solid var(--line);color:var(--red-text);font-family:var(--head);font-weight:700;font-size:16px;display:flex;align-items:center;justify-content:center;background:var(--white)}
.appt-note{top:414px;font-size:14px;color:#444}

/* footer */
.site-footer{top:3588px;left:0;width:1200px;height:320px;background:var(--ink);color:var(--white)}
.foot-head{top:80px;font-family:var(--head);font-weight:500;font-size:16px}
.foot-list{top:108px;font-size:14px;line-height:28px}
.social{top:109px;left:922px;display:flex;gap:9px}
.social i{display:block;width:34px;height:34px;border:2px solid var(--white);border-radius:50%}
.pay{top:168px;left:922px;font-family:var(--body);font-weight:600;font-size:30px;display:flex;align-items:center;gap:10px}
.pay b{display:block;width:22px;height:22px;background:var(--white)}
.copyright{top:262px;left:0;width:1200px;height:58px;border-top:1px solid #3b3d46;text-align:center;font-size:14px;line-height:54px}
</style>
</head>
<body>
<div class="page">

<header class="site-header abs">
  <div class="brand abs">
    <div class="brand-name">BRENVASHINE</div>
    <div class="brand-sub">BODYSHOP</div>
  </div>
  <div class="top-contact abs" style="left:702px">
    <svg width="16" height="16" viewBox="0 0 24 24" fill="#fff"><path d="M6.6 10.8a15 15 0 0 0 6.6 6.6l2.2-2.2c.3-.3.7-.4 1-.2 1.1.4 2.3.6 3.6.6.6 0 1 .4 1 1V20c0 .6-.4 1-1 1A17 17 0 0 1 3 4c0-.6.4-1 1-1h3.5c.6 0 1 .4 1 1 0 1.3.2 2.5.6 3.6.1.3 0 .7-.2 1z"/></svg>
    07700 914 552
  </div>
  <div class="top-contact abs" style="left:858px">
    <svg width="18" height="14" viewBox="0 0 18 14" fill="none" stroke="#fff" stroke-width="1.6"><rect x="1" y="1" width="16" height="12"/><path d="M1 1l8 7 8-7"/></svg>
    sales@brenvashine.co.uk
  </div>
  <nav class="nav abs">
    <span class="active" style="left:502px">HOME</span>
    <span style="left:570px">ABOUT US</span>
    <span style="left:670px">SERVICE</span>
    <span style="left:757px">STORE</span>
    <span style="left:828px">CUSTOM</span>
    <span style="left:919px">GALLERY</span>
    <span style="left:1009px">CONTACT</span>
  </nav>
</header>

<section class="hero abs" role="img" aria-label="Sports car speeding along a motion-blurred road with streaks of light">
  <div class="hero-title abs center">BRENVASHINE BODYSHOP</div>
  <div class="hero-sub abs center">YOUR ONE STOP BODY SHOP<br>The home of paint perfection</div>
  <div class="hero-btn abs">GET STARTED</div>
  <div class="dots abs"><i></i><i class="on"></i><i></i></div>
</section>

<section class="welcome">
  <h1 class="welcome-title abs center">WELCOME TO<br><span style="font-size:30px">BRENVASHINE YOUR ONE STOP BODYSHOP</span></h1>
  <p class="welcome-text abs">Fully qualified trained technicians family run business established over 30 years Brenvashine, based in Ashvale, Northmoor established in August, 1985 has grown to become Northmoor's premiere manufacturer approved accident repair centre.</p>
  <div class="outline-btn abs">READ MORE
    <svg width="16" height="16" viewBox="0 0 16 16"><circle cx="8" cy="8" r="8" fill="#c41e2e"/><path d="M6 4l4 4-4 4" stroke="#fff" stroke-width="2" fill="none"/></svg>
  </div>

  <svg class="abs" style="left:80px;top:1265px" width="22" height="30" viewBox="0 0 22 30"><path d="M18 3L6 15l12 12" stroke="#777" stroke-width="5" fill="none"/></svg>
  <svg class="abs" style="left:1094px;top:1265px" width="22" height="30" viewBox="0 0 22 30"><path d="M4 3l12 12L4 27" stroke="#777" stroke-width="5" fill="none"/></svg>

  <div class="photo-round abs" style="left:179px;top:1168px;width:222px;height:222px;background:radial-gradient(circle at 55% 45%,#3a5b9a,#1b1f2a 60%,#0c0d10)" role="img" aria-label="Polishing machine buffing a black car panel"></div>
  <div class="circle-label abs" style="left:140px;top:1404px">CAR BODY REPAIRS</div>

  <div class="feature abs">
    <h3>WHEEL PAINTING</h3>
    <p>Lorem ipsum dolor sit amadipiscing elit, sed do tempor incididunt ut labore et magna aliqua.</p>
    <svg style="margin-top:16px" width="42" height="42" viewBox="0 0 42 42"><circle cx="21" cy="21" r="19" stroke="#fff" stroke-width="2" fill="none"/><circle cx="21" cy="21" r="11" fill="#fff"/><path d="M19 16l5 5-5 5" stroke="#7e1520" stroke-width="2.5" fill="none"/></svg>
  </div>

  <div class="photo-round abs" style="left:801px;top:1168px;width:222px;height:222px;background:radial-gradient(circle at 50% 60%,#b3202a,#4c4f55 55%,#7a8a6a)" role="img" aria-label="Red custom painted motorcycle parked by a fence"></div>
  <div class="circle-label abs" style="left:762px;top:1404px">MOTORCYCLE PAINTING</div>
</section>

<section class="services abs">
  <div class="services-photo abs" role="img" aria-label="Black car front split with a glowing blue wireframe view of the same car"></div>
  <h2 class="abs">OUR SERVICES</h2>
  <div class="svc abs" style="top:150px"><span class="svc-ico"><svg width="50" height="30" viewBox="0 0 50 30" fill="none" stroke="#fff" stroke-width="3"><path d="M4 22h42v-6l-8-2-6-8H16l-6 8-6 2z"/><circle cx="14" cy="24" r="4" fill="#fff"/><circle cx="36" cy="24" r="4" fill="#fff"/></svg></span>FULL OR PART RESPRAYS</div>
  <div class="svc abs" style="top:253px"><span class="svc-ico"><svg width="44" height="44" viewBox="0 0 44 44" fill="none" stroke="#fff" stroke-width="4"><path d="M10 34L30 14"/><circle cx="32" cy="12" r="6"/><path d="M8 36l4-4"/></svg></span>DENTS &amp; SCRATCH REMOVAL</div>
  <div class="svc abs" style="top:357px"><span class="svc-ico"><svg width="48" height="48" viewBox="0 0 48 48" fill="none" stroke="#fff" stroke-width="3"><circle cx="24" cy="24" r="20"/><circle cx="24" cy="24" r="6"/><path d="M24 4v14M24 30v14M4 24h14M30 24h14"/></svg></span>BUMPER REPAIR</div>
  <div class="svc abs" style="top:460px"><span class="svc-ico"><svg width="50" height="30" viewBox="0 0 50 30" fill="none" stroke="#fff" stroke-width="3"><path d="M4 22h42v-7l-10-3-6-7"/><circle cx="14" cy="24" r="4" fill="#fff"/><circle cx="36" cy="24" r="4" fill="#fff"/></svg></span>ACCIDENT REPAIR</div>
  <div class="svc abs" style="top:562px"><span class="svc-ico"><svg width="40" height="44" viewBox="0 0 40 44" fill="#fff"><rect x="14" y="4" width="14" height="12"/><rect x="18" y="16" width="6" height="24"/><path d="M4 10h8M2 16h10M4 22h8" stroke="#fff" stroke-width="2.5"/></svg></span>ALLOY WHEEL'S REFURBISHED,<br>&amp; PAINTED</div>
</section>

<section class="gallery">
  <h2 class="section-title abs center" style="top:2342px">OUR GALLERY</h2>
  <div class="thumb abs" style="left:111px;top:2427px;background:linear-gradient(135deg,#6a7050,#3a3e2c)" role="img" aria-label="Olive green vintage motorcycle"></div>
  <div class="thumb abs" style="left:362px;top:2427px;background:linear-gradient(135deg,#9a9a9a,#2a2a2a)" role="img" aria-label="Black cruiser motorcycle in a workshop"></div>
  <div class="thumb abs" style="left:613px;top:2427px;background:linear-gradient(135deg,#a58a66,#c4242c 60%,#2a2a2a)" role="img" aria-label="Red sports car with black stripes in front of a building"></div>
  <div class="thumb abs" style="left:864px;top:2427px;background:linear-gradient(135deg,#c9c6c0,#eceae6 50%,#6a6a6a)" role="img" aria-label="White saloon car front view"></div>
  <div class="thumb abs" style="left:111px;top:2618px;background:linear-gradient(135deg,#2a70b8,#1a1a1a 55%,#888)" role="img" aria-label="Blue and chrome custom motorcycle"></div>
  <div class="thumb abs" style="left:362px;top:2618px;background:linear-gradient(135deg,#3b8eb0,#1a5f7d 55%,#aaa)" role="img" aria-label="Light blue classic car in a paint shop"></div>
  <div class="thumb abs" style="left:613px;top:2618px;background:linear-gradient(135deg,#888,#111 55%,#333)" role="img" aria-label="Black hatchback with rear spoiler"></div>
  <div class="thumb abs" style="left:864px;top:2618px;background:linear-gradient(135deg,#ddd,#8a8a8a 55%,#555)" role="img" aria-label="Silver saloon car in a workshop"></div>
</section>

<section class="partners">
  <h2 class="section-title abs center" style="top:2857px">OUR PARTNERS</h2>
  <svg class="abs" style="left:70px;top:2948px" width="20" height="34" viewBox="0 0 20 34"><path d="M16 2L3 17l13 15" stroke="#333" stroke-width="2" fill="none"/></svg>
  <svg class="abs" style="left:1112px;top:2948px" width="20" height="34" viewBox="0 0 20 34"><path d="M4 2l13 15L4 32" stroke="#333" stroke-width="2" fill="none"/></svg>
  <div class="partner abs" style="left:111px">Q WRAP</div>
  <div class="partner abs" style="left:362px">GLENBRUSH</div>
  <div class="partner abs" style="left:613px">DORFLINT</div>
  <div class="partner abs" style="left:864px">VASTINCO</div>
</section>

<section class="appointment abs">
  <h2 class="section-title abs center">APPOINTMENT</h2>
  <div class="appt-addr abs center">BRENVASHINE BODYSHOP,HARROWGATE TRADE PARK,<br>KILN ROAD,ASHVALE,NORTHMOOR,NM14 7QZ</div>
  <div class="field abs" style="left:299px;top:214px;width:293px">Date :</div>
  <div class="field abs" style="left:607px;top:214px;width:294px">Time :</div>
  <div class="field abs" style="left:299px;top:282px;width:602px">Price :</div>
  <div class="submit abs">SUBMIT</div>
  <div class="appt-note abs center">If You Are Unable to Keep Your Appointment, Please Contact Us Soon As Possible</div>
</section>

<footer class="site-footer abs">
  <div class="brand abs" style="left:114px;top:72px;width:300px">
    <div class="brand-name" style="font-size:34px;letter-spacing:2px;line-height:40px">BRENVASHINE</div>
    <div class="brand-sub" style="font-size:15px;letter-spacing:12px">BODYSHOP</div>
  </div>
  <div class="foot-head abs" style="left:489px">CONTACT US</div>
  <div class="foot-list abs" style="left:489px">
    <div><svg width="10" height="13" viewBox="0 0 10 13" fill="#fff"><path d="M5 0a5 5 0 0 0-5 5c0 4 5 8 5 8s5-4 5-8a5 5 0 0 0-5-5zm0 7a2 2 0 1 1 0-4 2 2 0 0 1 0 4z"/></svg> Harrowgate Trade Park,</div>
    <div style="padding-left:15px">Kiln Road, Ashvale,</div>
    <div style="padding-left:15px">Northmoor,NM14 7QZ</div>
    <div><svg width="11" height="11" viewBox="0 0 24 24" fill="#fff"><path d="M6.6 10.8a15 15 0 0 0 6.6 6.6l2.2-2.2c.3-.3.7-.4 1-.2 1.1.4 2.3.6 3.6.6.6 0 1 .4 1 1V20c0 .6-.4 1-1 1A17 17 0 0 1 3 4c0-.6.4-1 1-1h3.5c.6 0 1 .4 1 1 0 1.3.2 2.5.6 3.6.1.3 0 .7-.2 1z"/></svg> 07700 914 552</div>
    <div><svg width="13" height="10" viewBox="0 0 18 14" fill="none" stroke="#fff" stroke-width="1.8"><rect x="1" y="1" width="16" height="12"/><path d="M1 1l8 7 8-7"/></svg> sales@brenvashine.co.uk</div>
  </div>
  <div class="foot-head abs" style="left:727px">SUPPORT</div>
  <div class="foot-list abs" style="left:727px">
    <div>Contact</div><div>&nbsp;FAQ's</div><div>Returns</div><div>Terms &amp; Conditions</div>
  </div>
  <div class="foot-head abs" style="left:922px">SOCIAL</div>
  <div class="social abs" aria-label="Social profiles"><i></i><i></i><i></i><i></i></div>
  <div class="pay abs"><b></b>TILLWAVE</div>
  <div class="copyright abs">Copyright © 2019. All Rights Reserved</div>
</footer>

</div>
</body>
</html>
```